PillPeak website blog. Simple medical advice given in clear yes or no answers that save people money

I am developing a new web page that provides medical care cost savings at the consumers' fingertips. I need a web page that is clean, concise, and attractive for me to put my valuable medical information on. The information I provide is simple to obtain, yet very valuable to the consumer, and answered in a yes or no format. For example, A person may wonder if they need an antibiotic for cold like symptoms. Seeing a doctor for an antibiotic is very expensive. But with simple and clear advice at their fingertips, they can confidently avoid having to pay $200 or more to see a doctor and get an antibiotic. This is kind of like consumer reports for medical services.

Target Market(s)

People who are savvy shoppers and want to save money on healthcare. Likely younger ages between 21 and 60, who are mobile, readily use iphones, and want strong evidence based research to guide their decisions.

Industry/Entity Type

Coding

Number of Pages Required

Colors

Requirements
Must have
• A template on the "Question" and "Answer" page that can be edited many times that can be edited many times. The Confidence rating scale would need to be edited as well. The "Date Researched" the "PillPeak Pilluminate" and "References" all need to be able to be edited. This website must be very clear and simple to understand. A medical question is posed with a yes or no answer, then answered and given a confidence rating, we then tell them how much money they saved by going to our website.
Nice to have
• We want this to be slightly fun, vibrant, warm and inviting. This will be sometime later converted into an app format. Quirky, some humor to keep it interesting.
Should not have
• No sterile looking medical images. Not boring.

```html
<!DOCTYPE html>
<html lang="en">
<head>
<meta charset="utf-8">
<title>PillPeak</title>
<link href="https://fonts.googleapis.com/css2?family=Lato:wght@400;700;900&display=swap" rel="stylesheet">
<style>
  :root {
    --brand-blue: #1560ad;
    --brand-blue-line: #2f78c4;
    --brand-red: #e4002b;
    --ink: #333333;
    --muted: #6f6f6f;
    --panel: #f2f2f2;
    --panel-border: #bdbdbd;
    --white: #ffffff;
  }
  * { box-sizing: border-box; margin: 0; padding: 0; }
  html, body { width: 1200px; height: 831px; overflow: hidden; background: var(--white); }
  body { font-family: 'Lato', sans-serif; color: var(--ink); position: relative; }

  .site-header { position: absolute; left: 0; top: 0; width: 1200px; height: 155px; }
  .brand { position: absolute; left: 76px; top: 38px; display: flex; align-items: center; gap: 12px; }
  .brand-dot { width: 62px; height: 62px; border-radius: 50%; background: var(--brand-blue); }
  .brand-name { font-size: 32px; font-weight: 700; color: var(--brand-red); }
  .tagline { position: absolute; right: 74px; top: 63px; font-size: 24px; font-weight: 700; color: var(--brand-blue); letter-spacing: 0.2px; }

  .main-nav { position: absolute; left: 0; top: 155px; width: 1200px; height: 47px; background: var(--brand-red); }
  .main-nav ul { list-style: none; position: absolute; left: 74px; top: 0; height: 47px; display: flex; align-items: center; gap: 37px; }
  .main-nav li { color: var(--white); font-size: 13px; font-weight: 700; text-transform: uppercase; }
  .search-box { position: absolute; left: 960px; top: 8px; width: 166px; height: 31px; background: var(--white); border-radius: 3px; display: flex; align-items: center; justify-content: space-between; padding: 0 10px; font-size: 13px; color: var(--ink); }

  .side-menu { position: absolute; left: 0; top: 202px; width: 314px; height: 379px; background: var(--brand-blue); list-style: none; }
  .side-menu li { height: 53px; border-bottom: 1px solid var(--brand-blue-line); display: flex; align-items: center; padding-left: 75px; color: var(--white); font-size: 13px; font-weight: 700; text-transform: uppercase; }
  .side-menu li:last-child { border-bottom: none; }

  .hero { position: absolute; left: 314px; top: 202px; width: 886px; height: 379px; overflow: hidden; }
  .hero-photo { position: absolute; inset: 0; background: linear-gradient(90deg, #8d8a86 0%, #a8a7a5 30%, #b9b6b4 55%, #a88e94 80%, #8f7a7f 100%); }
  .hero-shade { position: absolute; inset: 0; background: rgba(40,40,40,0.25); }
  .hero-title { position: absolute; left: 0; right: 0; top: 124px; text-align: center; color: var(--white); font-size: 35px; font-weight: 900; line-height: 47px; }
  .hero-title .accent { color: var(--brand-red); }
  .hero-arrow { position: absolute; top: 177px; }
  .hero-arrow.prev { left: 30px; }
  .hero-arrow.next { right: 74px; }

  .disclaimer { position: absolute; left: 75px; top: 610px; width: 500px; }
  .disclaimer-label { font-size: 13px; font-weight: 700; color: var(--brand-red); margin-bottom: 6px; }
  .disclaimer-text { font-size: 13px; line-height: 23px; color: var(--ink); }
  .copyright { position: absolute; left: 74px; top: 742px; font-size: 13px; color: var(--muted); }
  .social { position: absolute; left: 74px; top: 771px; display: flex; gap: 19px; }
  .social span { width: 22px; height: 22px; border-radius: 50%; background: var(--muted); }

  .ask-card { position: absolute; left: 614px; top: 614px; width: 229px; height: 179px; background: var(--panel); border: 1px solid var(--panel-border); overflow: hidden; text-align: center; }
  .ask-ring { position: absolute; left: 22px; top: 3px; width: 172px; height: 172px; border-radius: 50%; border: 4px solid #c4c4c4; background: #dde6ef; }
  .ask-text { position: relative; padding-top: 38px; font-weight: 700; }
  .ask-title { color: var(--brand-red); font-size: 21px; line-height: 25px; }
  .ask-note { color: var(--brand-blue); font-size: 18px; line-height: 25px; margin-top: 4px; }

  .signup-card { position: absolute; left: 857px; top: 614px; width: 269px; height: 179px; background: var(--panel); border: 1px solid var(--panel-border); }
  .signup-title { position: absolute; left: 11px; top: 26px; font-size: 18px; font-weight: 700; color: var(--brand-blue); }
  .signup-input { position: absolute; left: 11px; top: 62px; width: 245px; height: 42px; background: var(--white); border: 1px solid var(--panel-border); font-size: 13px; padding-left: 13px; display: flex; align-items: center; color: var(--ink); }
  .signup-submit { position: absolute; left: 149px; top: 111px; width: 107px; height: 37px; background: var(--brand-red); color: var(--white); font-size: 15px; font-weight: 700; display: flex; align-items: center; justify-content: center; border-radius: 2px; }
</style>
</head>
<body>
  <header class="site-header">
    <div class="brand"><span class="brand-dot"></span><span class="brand-name">PillPeak</span></div>
    <p class="tagline">CLEAR . VALUABLE. HEALTH. DEVICE. RIGHT NOW</p>
  </header>

  <nav class="main-nav">
    <ul>
      <li>Prev/Screening</li><li>Women's Health</li><li>Men's Health</li><li>Med's</li>
      <li>Surgery</li><li>Imaging</li><li>Peds</li><li>Controversion</li>
    </ul>
    <div class="search-box">
      <span>Search..</span>
      <svg width="15" height="15" viewBox="0 0 15 15"><circle cx="6" cy="6" r="4.5" fill="none" stroke="#333" stroke-width="2"/><line x1="9.5" y1="9.5" x2="14" y2="14" stroke="#333" stroke-width="2.4" stroke-linecap="round"/></svg>
    </div>
  </nav>

  <ul class="side-menu">
    <li>Who we are?</li><li>How&nbsp; it works</li><li>How we know</li><li>Endurance based research</li>
    <li>Dr. Hosting</li><li>Who we are not</li><li>Are we baised</li>
  </ul>

  <section class="hero">
    <div class="hero-photo" role="img" aria-label="Photo of a doctor showing a tablet to an older patient in a clinic"></div>
    <div class="hero-shade"></div>
    <svg class="hero-arrow prev" width="18" height="30" viewBox="0 0 18 30"><polyline points="15,3 4,15 15,27" fill="none" stroke="#fff" stroke-width="4" stroke-linecap="round" stroke-linejoin="round"/></svg>
    <h1 class="hero-title">SAVE $1000&nbsp; PER YEAR ON<br>HEALTHCARE <span class="accent">IT'S FREE</span></h1>
    <svg class="hero-arrow next" width="18" height="30" viewBox="0 0 18 30"><polyline points="3,3 14,15 3,27" fill="none" stroke="#fff" stroke-width="4" stroke-linecap="round" stroke-linejoin="round"/></svg>
  </section>

  <section class="disclaimer">
    <h2 class="disclaimer-label">DISCLAIMER:</h2>
    <p class="disclaimer-text">Lorem ipsum dolor sit amet, consectetur adipiscing elit. Duis nec enim lorem. Duis mollis nunc mauris.&nbsp; Etiam imperdiet est a urna elementum, ac viverra tellus feugiat. Nunc et nisi ut dolor lobortis pretium id id nunc. Vivamus eu libero ac nibh auctor rhoncus. Fusce ex felis, sollicitudin non velit quis, auctor suscipit dolor.</p>
  </section>
  <p class="copyright">Copyright © 2018. Company Name. All Right Reserved</p>
  <div class="social" aria-label="Social links"><span></span><span></span><span></span><span></span><span></span></div>

  <aside class="ask-card">
    <div class="ask-ring"></div>
    <div class="ask-text">
      <p class="ask-title">ASK A<br>QUESTION&nbsp; HERE!</p>
      <p class="ask-note">IF IT IS WORKING WELL<br>WE WILL POST</p>
    </div>
  </aside>

  <aside class="signup-card">
    <h3 class="signup-title">BECOME A MED TODAY!</h3>
    <div class="signup-input">Enter Email Address</div>
    <div class="signup-submit">SUBMIT</div>
  </aside>
</body>
</html>
```